Coastline Premier Retreats Business Card Design

Design a business card for Coastline Premier Retreats. Look at the website for colors and reference. Card should have logo, name, title, office number, mobile number, email, URL and a tagline like, "Luxury Hotel & Resort Email Marketing" (This might change).

https://www.coastlinepremierretreats.example

The rest I will leave up to your imagination.

Contact Information for Business Card

Logo, name, title, office number, mobile number, email, URL and a tagline like, "Luxury Hotel & Resort Email Marketing" (This might change).

```html
<!DOCTYPE html>
<html lang="en">
<head>
<meta charset="utf-8">
<title>Coastline Premier Retreats – Business Card</title>
<link href="https://fonts.googleapis.com/css2?family=Open+Sans:wght@400;600;700&display=swap" rel="stylesheet">
<style>
  :root {
    --stage: #232323;
    --card: #222226;
    --card-fold: #28282d;
    --card-fold-deep: #2d2d33;
    --accent: #f47a20;
    --ink: #ffffff;
    --ink-soft: #e9e9ec;
  }
  * { box-sizing: border-box; margin: 0; padding: 0; }
  html, body {
    width: 1200px; height: 780px; overflow: hidden;
    background: var(--stage);
    font-family: "Open Sans", Arial, sans-serif;
  }
  .stage {
    position: relative; width: 1200px; height: 780px;
    display: flex; justify-content: center; align-items: center; gap: 70px;
  }
  .card {
    position: relative; width: 380px; height: 664px;
    background: var(--card); border-radius: 22px; overflow: hidden;
    box-shadow: 0 18px 40px rgba(0,0,0,.55);
  }

  /* Front */
  .front-mark {
    position: absolute; left: 50%; top: 50%;
    transform: translate(-50%, -50%) rotate(-90deg);
    display: flex; align-items: center; gap: 18px; white-space: nowrap;
  }
  .front-mark .mark-square {
    width: 22px; height: 22px; background: var(--accent); flex: none;
  }
  .front-mark .mark-name {
    color: var(--ink); font-weight: 700; font-size: 30px;
    letter-spacing: 2px; text-transform: uppercase;
  }

  /* Back */
  .back-folds { position: absolute; inset: 0; width: 100%; height: 100%; }
  .back-brand {
    position: absolute; top: 64px; left: 0; right: 0;
    display: flex; justify-content: center; align-items: center; gap: 10px;
  }
  .back-brand .mark-square { width: 12px; height: 12px; background: var(--accent); }
  .back-brand .mark-name {
    color: var(--ink); font-weight: 700; font-size: 15px;
    letter-spacing: 1.5px; text-transform: uppercase;
  }
  .identity { position: absolute; top: 230px; left: 0; right: 0; text-align: center; }
  .person-name { font-weight: 700; font-size: 30px; line-height: 1.1; }
  .person-name .first { color: var(--accent); }
  .person-name .last { color: var(--ink); }
  .person-title { color: var(--ink-soft); font-size: 14px; margin-top: 4px; }
  .contact-icons { display: flex; justify-content: center; gap: 10px; margin-top: 18px; }
  .contact-icons svg { width: 26px; height: 26px; }
  .contact-list { list-style: none; margin-top: 14px; color: var(--ink); font-size: 14px; line-height: 1.55; }
  .tagline {
    position: absolute; bottom: 62px; left: 0; right: 0; text-align: center;
    color: var(--accent); font-size: 16px; line-height: 1.35;
  }
</style>
</head>
<body>
<main class="stage">
  <section class="card card-front">
    <div class="front-mark">
      <span class="mark-square"></span>
      <span class="mark-name">Coastline Premier Retreats</span>
    </div>
  </section>

  <section class="card card-back">
    <svg class="back-folds" viewBox="0 0 380 664" preserveAspectRatio="none" aria-hidden="true">
      <path d="M0 430 Q140 560 380 470 L380 664 L0 664 Z" fill="var(--card-fold)"/>
      <path d="M0 560 Q200 520 380 500 L380 664 L0 664 Z" fill="var(--card-fold-deep)"/>
      <path d="M0 420 Q190 540 380 380 L380 400 Q190 560 0 440 Z" fill="#1c1c20" opacity=".6"/>
    </svg>

    <div class="back-brand">
      <span class="mark-square"></span>
      <span class="mark-name">Coastline Premier Retreats</span>
    </div>

    <div class="identity">
      <h1 class="person-name"><span class="first">Marta</span> <span class="last">Kovalenko</span></h1>
      <p class="person-title">Co-Founder</p>
      <div class="contact-icons">
        <svg viewBox="0 0 26 26" aria-label="Office phone"><circle cx="13" cy="13" r="13" fill="var(--accent)"/><path d="M9 8c1 0 2 2 2 3l-1 1c.6 1.6 1.8 2.8 3.4 3.4l1-1c1 0 3 1 3 2l-1 1.5C12 18 8 14 7.5 9.5Z" fill="#fff"/></svg>
        <svg viewBox="0 0 26 26" aria-label="Mobile phone"><circle cx="13" cy="13" r="13" fill="var(--accent)"/><rect x="9.5" y="6.5" width="7" height="13" rx="1.5" fill="none" stroke="#fff" stroke-width="1.5"/></svg>
        <svg viewBox="0 0 26 26" aria-label="Email"><circle cx="13" cy="13" r="13" fill="var(--accent)"/><rect x="7" y="9" width="12" height="9" fill="none" stroke="#fff" stroke-width="1.5"/><path d="M7 9l6 5 6-5" fill="none" stroke="#fff" stroke-width="1.5"/></svg>
        <svg viewBox="0 0 26 26" aria-label="Website"><circle cx="13" cy="13" r="13" fill="var(--accent)"/><circle cx="13" cy="13" r="6" fill="none" stroke="#fff" stroke-width="1.5"/><path d="M7 13h12M13 7c-3 3-3 9 0 12M13 7c3 3 3 9 0 12" fill="none" stroke="#fff" stroke-width="1.2"/></svg>
      </div>
      <ul class="contact-list">
        <li>(555) 214-3086</li>
        <li>(555) 430-7712</li>
        <li>www.coastlinepremierretreats.example</li>
        <li>info@coastlinepremierretreats.example</li>
      </ul>
    </div>

    <p class="tagline">Luxury Hotel &amp;<br>Resort Email Marketing</p>
  </section>
</main>
</body>
</html>
```